Business card design needed

I would like a one sided black business card with the information provided above. Refer to my website www.brightvolleyracquets.com.au for an example of colors I have used for my site, would like to keep this consistent for my business cards also, I will upload my logo below.

I am a new small business that provides tennis customers with racquet re stringing, tennis strings and accessories.

Industry/Entity Type

Small Business

Contact Information for Business Card

Bright Volley Tennis

Owen Whitby
Managing Director

brightvolleyracquets@mailbox.example
www.brightvolleyracquets.com.au
0491 726 305

Racquet Restringing/Tennis Strings/Accessories

Requirements
Must have
• Must have my logo and card must be black

```html
<!DOCTYPE html>
<html lang="en">
<head>
<meta charset="utf-8">
<title>Bright Volley Tennis – Business Card</title>
<link rel="stylesheet" href="https://fonts.googleapis.com/css2?family=Roboto:wght@400;700&display=swap">
<style>
  :root {
    --backdrop: #a8683f;
    --card: #000000;
    --lime: #b5d334;
    --navy: #2b4a7e;
    --white: #ffffff;
    --grey: #e6e6e6;
  }
  * { box-sizing: border-box; margin: 0; padding: 0; }
  html, body {
    width: 1200px; height: 475px; overflow: hidden;
    background: var(--backdrop);
    font-family: "Roboto", Arial, sans-serif;
  }
  .stage { position: relative; width: 1200px; height: 475px; }
  .card {
    position: absolute; top: 81px;
    width: 549px; height: 313px;
    background: var(--card);
    overflow: hidden;
  }
  .card--front { left: 42px; }
  .card--back { left: 602px; }

  .edge-stripe { position: absolute; left: 0; width: 10px; }
  .edge-stripe--navy { top: 0; height: 180px; background: var(--navy); }
  .edge-stripe--lime { top: 185px; bottom: 0; background: var(--lime); }

  .brand {
    position: absolute; top: 100px;
    display: flex; align-items: center; gap: 10px;
    transform: translateX(-50%);
    white-space: nowrap;
  }
  .card--front .brand { left: 275px; }
  .card--back .brand { left: 272px; top: 108px; }
  .brand__dot {
    width: 30px; height: 30px; border-radius: 50%;
    background: var(--lime);
  }
  .brand__name {
    font-weight: 700; font-size: 30px;
    text-transform: uppercase; letter-spacing: 0.5px;
    color: var(--lime);
  }

  .person {
    position: absolute; left: 100px; top: 238px; width: 155px;
    text-align: center;
  }
  .person__name {
    font-size: 18px; font-weight: 400; letter-spacing: 0.5px;
    text-transform: uppercase; color: var(--lime);
  }
  .person__role { font-size: 14px; color: var(--lime); margin-top: 2px; }

  .contacts {
    position: absolute; left: 268px; top: 226px;
    list-style: none;
  }
  .contacts__item {
    display: flex; align-items: center; gap: 11px;
    height: 21px;
    font-size: 13px; color: var(--white);
    white-space: nowrap;
  }
  .contacts__item:first-child { font-size: 16px; }
  .contacts__icon { width: 11px; height: 11px; flex: none; }

  .back-url {
    position: absolute; left: 0; right: 0; top: 250px;
    text-align: center;
    font-size: 14px; letter-spacing: 2px; color: var(--grey);
  }
</style>
</head>
<body>
<div class="stage">
  <section class="card card--front" aria-label="Business card front">
    <span class="edge-stripe edge-stripe--navy"></span>
    <span class="edge-stripe edge-stripe--lime"></span>

    <div class="brand">
      <span class="brand__dot"></span>
      <span class="brand__name">Bright Volley Tennis</span>
    </div>

    <div class="person">
      <p class="person__name">Owen Whitby</p>
      <p class="person__role">Managing Director</p>
    </div>

    <ul class="contacts">
      <li class="contacts__item">
        <svg class="contacts__icon" viewBox="0 0 12 12" aria-hidden="true">
          <path d="M3 1 L5 3.5 L4 5 Q5.5 7 7 8 L8.5 7 L11 9 L9.5 11 Q4 10 1 2.5 Z" fill="var(--white)"/>
        </svg>
        <span>0491 726 305</span>
      </li>
      <li class="contacts__item">
        <svg class="contacts__icon" viewBox="0 0 12 12" aria-hidden="true">
          <rect x="0.5" y="2.5" width="11" height="7.5" fill="var(--white)"/>
          <path d="M0.5 2.5 L6 7 L11.5 2.5" fill="none" stroke="var(--card)" stroke-width="1.2"/>
        </svg>
        <span>brightvolleyracquets@mailbox.example</span>
      </li>
      <li class="contacts__item">
        <svg class="contacts__icon" viewBox="0 0 12 12" aria-hidden="true">
          <g fill="none" stroke="var(--white)" stroke-width="1.1">
            <circle cx="6" cy="6" r="5"/>
            <ellipse cx="6" cy="6" rx="2.2" ry="5"/>
            <path d="M1 6 H11 M2 3.5 H10 M2 8.5 H10"/>
          </g>
        </svg>
        <span>www.brightvolleyracquets.com.au</span>
      </li>
    </ul>
  </section>

  <section class="card card--back" aria-label="Business card back">
    <div class="brand">
      <span class="brand__dot"></span>
      <span class="brand__name">Bright Volley Tennis</span>
    </div>
    <p class="back-url">www.brightvolleyracquets.com.au</p>
  </section>
</div>
</body>
</html>
```